Classy, Elegant, Simple Business Card Design

Looking to have a classy, simple, and elegant design. Want a top notch designed business card. I really like the look of the new torvane credit card. I also like the design I attached. I am trying to reach 21-29 year old females for booking us for there wedding or event. We offer Disc Jockey Service, Photo Booth Rentals, and Uplighting .

Target Market(s)

21-28 year old females

Contact Information for Business Card

Has to have logo, website, email, and phone number

Font styles to use
Other font styles liked:
• open to font choice, modern, clean
Designer to choose
33a6d7
0791cd
0555a3
ffffff

Requirements
Must have
• Has to have logo, website, email, and phone number
Nice to have
• I really like the design of the new torvane credit card. I also included my logo and some designs I like
Should not have
• clutter or too much info

```html
<!DOCTYPE html>
<html lang="en">
<head>
<meta charset="utf-8">
<title>Tidewell Event Group — Business Card</title>
<link href="https://fonts.googleapis.com/css2?family=Jost:wght@400&display=swap" rel="stylesheet">
<style>
  :root {
    --backdrop: #f4f4f4;
    --card: #ffffff;
    --card-edge: #e6e6e6;
    --silver: #a9a9a9;
    --ink: #8a8a8a;
    --ink-strong: #7d7d7d;
  }
  * { margin: 0; padding: 0; box-sizing: border-box; }
  html, body {
    width: 1200px;
    height: 900px;
    overflow: hidden;
    background: var(--backdrop);
    font-family: "Jost", "Futura", sans-serif;
  }
  .canvas {
    position: relative;
    width: 1200px;
    height: 900px;
  }
  .card {
    position: absolute;
    left: 292px;
    width: 617px;
    height: 352px;
    background: var(--card);
    border: 1px solid var(--card-edge);
    border-radius: 22px;
  }
  .card--front { top: 76px; }
  .card--back { top: 472px; }

  .wordmark {
    position: absolute;
    left: 0;
    right: 0;
    top: 144px;
    text-align: center;
    color: var(--silver);
    font-weight: 400;
    line-height: 1;
  }
  .wordmark__name {
    display: block;
    font-size: 40px;
    letter-spacing: 1px;
  }
  .wordmark__sub {
    display: block;
    margin-top: 4px;
    font-size: 18px;
    letter-spacing: 8px;
    padding-left: 8px;
  }

  .brand-dot {
    position: absolute;
    left: 42px;
    top: 64px;
  }

  .contact {
    position: absolute;
    left: 42px;
    top: 188px;
    color: var(--ink);
  }
  .contact__name {
    font-size: 21px;
    color: var(--ink-strong);
    letter-spacing: 0.5px;
    margin-bottom: 14px;
  }
  .contact__line {
    font-size: 16px;
    line-height: 25px;
  }
</style>
</head>
<body>
  <main class="canvas">
    <section class="card card--front" aria-label="Card front">
      <div class="wordmark">
        <span class="wordmark__name">TIDEWELL</span>
        <span class="wordmark__sub">EVENT GROUP</span>
      </div>
    </section>

    <section class="card card--back" aria-label="Card back">
      <svg class="brand-dot" width="64" height="64" viewBox="0 0 64 64" aria-hidden="true">
        <circle cx="32" cy="32" r="30" fill="var(--silver)"/>
      </svg>
      <div class="contact">
        <p class="contact__name">Daniel R. Hale</p>
        <p class="contact__line">555 014 2290</p>
        <p class="contact__line">hello@tidewelleventgroup.com</p>
        <p class="contact__line">www.tidewelleventgroup.com</p>
      </div>
    </section>
  </main>
</body>
</html>
```